Update the A4 Specials Page for Restaurant/Cafe

Provide a MINIMALIST attractive Specials page we can print weekly for our food and drink specials to give to our guests. Final design is to be provided in WORD Document so it can be easily edited by Manager. Should be black text and MINIMALIST to minimise ink usage as we print hundreds a week. We have UPLOADED the existing page as a template for you to update. Maybe logo can stay, see what you think. Or delete it and do something else. Keep it simple. Choose a good FONT. Could be a little playful with a cocktail ICON or something. Our existing menus can be seen at www.saltmeadowcafe.com.au and they are using font Alegreya. Please note we are unable to provide any feedback to designers, however we really do appreciate your time if you are submitting a design. Thank you for your participation.

```html
<!DOCTYPE html>
<html lang="en">
<head>
<meta charset="utf-8">
<title>Weekly Specials</title>
<link href="https://fonts.googleapis.com/css2?family=Alegreya:wght@400;500&family=Alegreya+SC:wght@900&display=swap" rel="stylesheet">
<style>
  :root {
    --backdrop: #e8e6e3;
    --paper: #ffffff;
    --frame: #3f676e;
    --ink: #3a5f66;
    --divider-light: #d6d8d8;
    --divider-mid: #b9bdbe;
  }
  * { margin: 0; padding: 0; box-sizing: border-box; }
  html, body {
    width: 1200px;
    height: 544px;
    overflow: hidden;
    background: var(--backdrop);
  }
  .specials-page {
    position: absolute;
    left: 422px;
    top: 14px;
    width: 356px;
    height: 516px;
    background: var(--paper);
    border: 5.5px solid var(--frame);
    color: var(--ink);
    font-family: "Alegreya", Georgia, serif;
    text-align: center;
  }
  .page-title {
    position: absolute;
    top: 24px;
    left: 0;
    right: 0;
    font-size: 25px;
    font-weight: 500;
    letter-spacing: 0.2px;
    line-height: 1;
  }
  .special {
    position: absolute;
    left: 0;
    right: 0;
  }
  .special-heading {
    font-size: 15px;
    font-weight: 400;
    line-height: 1;
    margin-bottom: 6px;
  }
  .dish-name {
    font-family: "Alegreya SC", Georgia, serif;
    font-weight: 900;
    font-size: 10px;
    letter-spacing: 0.2px;
    line-height: 13px;
  }
  .dish-desc {
    font-size: 8.5px;
    line-height: 13px;
  }
  .price {
    font-size: 13px;
    font-weight: 500;
    line-height: 15px;
    margin-top: 1px;
  }
  .price sup {
    font-size: 7px;
    vertical-align: 6px;
  }
  .divider {
    position: absolute;
    left: 56px;
    width: 233px;
    height: 8px;
  }
  .chicken-filo { top: 102px; }
  .minestrone { top: 200px; }
  .cocktail { top: 282px; }
  .craft-beer { top: 404px; }
  .divider-one { top: 169px; }
  .divider-two { top: 255px; }
  .divider-three { top: 378px; }
</style>
</head>
<body>
  <main class="specials-page">
    <h1 class="page-title">Weekly Specials</h1>

    <section class="special chicken-filo">
      <h2 class="dish-name">Chicken Filo</h2>
      <p class="dish-desc">Creamy Chicken with Pinenuts, wrapped in Filo Pastry.</p>
      <p class="dish-desc">Served with Side Salad &amp; Zulu Sauce</p>
      <p class="price"><sup>$</sup>24</p>
    </section>

    <svg class="divider divider-one" role="img" aria-label="Decorative flourish divider" viewBox="0 0 233 8">
      <defs>
        <linearGradient id="flourish-tone" x1="0" x2="1" y1="0" y2="0">
          <stop offset="0" stop-color="var(--divider-light)"/>
          <stop offset="0.5" stop-color="var(--divider-mid)"/>
          <stop offset="1" stop-color="var(--divider-light)"/>
        </linearGradient>
      </defs>
      <rect x="0" y="3" width="233" height="2" rx="1" fill="url(#flourish-tone)"/>
    </svg>

    <section class="special minestrone">
      <h2 class="dish-name">Minestrone Soup</h2>
      <p class="dish-desc">Served with Garlic Bread</p>
      <p class="price"><sup>$</sup>8</p>
    </section>

    <svg class="divider divider-two" role="img" aria-label="Decorative flourish divider" viewBox="0 0 233 8">
      <rect x="0" y="3" width="233" height="2" rx="1" fill="url(#flourish-tone)"/>
    </svg>

    <section class="special cocktail">
      <h2 class="special-heading">Cocktail Special</h2>
      <h3 class="dish-name">Passionista</h3>
      <p class="dish-desc">Vodka, Passionfruit Pulp, Mango Puree</p>
      <p class="dish-desc">Top up with Ginger &amp; Lemon Kombucha</p>
      <p class="price"><sup>$</sup>17</p>
    </section>

    <svg class="divider divider-three" role="img" aria-label="Decorative flourish divider" viewBox="0 0 233 8">
      <rect x="0" y="3" width="233" height="2" rx="1" fill="url(#flourish-tone)"/>
    </svg>

    <section class="special craft-beer">
      <h2 class="special-heading">Craft Beer Special</h2>
      <h3 class="dish-name">Sly Gecko<br>Sun Punch</h3>
      <p class="dish-desc">Tropical Pale Ale 4.8% Alc.</p>
      <p class="price"><sup>$</sup>10</p>
    </section>
  </main>
</body>
</html>
```